Food broker, trader, wholesaler, liquidator looking for a 5 pages website

Looking for a 5 pages website design. We are food brokers, traders, wholesaler and closeout buyer working with manufacturers, distributors, importers sell to retailers, food service operators and industrial (ingredients). We help market their products. We are a resource for those who need a solution in the distribution/selling/placement of food on the shelves, kitchens and pantries. Whether we open new accounts with new products or sell short dated inventory, we know where to go and get results.

Target Market(s)

Food manufacturers, food distributors, food brokers

Coding

Coded - Design and coding required

Number of Pages Required

4 page

Font styles to use
Serif

Requirements
Must have
• Food-food production-warehouse-Food packaging-people meeting-trucks-supermarket shelves-

```html
<!DOCTYPE html>
<html lang="en">
<head>
<meta charset="utf-8">
<title>Harborline Provisions</title>
<link href="https://fonts.googleapis.com/css2?family=Open+Sans:wght@400;600;700&display=swap" rel="stylesheet">
<style>
:root{
  --navy:#101a5c;
  --navy-deep:#0c0f4a;
  --band:#1c2a7a;
  --red:#ff0a0a;
  --red-text:#e5162c;
  --sky-top:#b6d3fb;
  --sky-low:#d7e6fb;
  --pale:#dde9fb;
  --cyan:#7fe0fb;
  --dark:#2b2b2b;
  --mint:#f6f9f0;
  --white:#ffffff;
  --line:#d8d8d8;
}
*{margin:0;padding:0;box-sizing:border-box}
html,body{width:1200px;height:3384px;overflow:hidden}
body{position:relative;font-family:"Open Sans",sans-serif;color:var(--navy);background:var(--white)}
.abs{position:absolute}
.center{left:0;width:1200px;text-align:center}
.backdrop{position:absolute;left:0;top:0}
.btn{position:absolute;background:var(--red);color:var(--white);font-weight:600;display:flex;align-items:center;justify-content:center;text-decoration:none}
.brand-mark{display:flex;flex-direction:column;align-items:center}
.brand-mark .dot{border-radius:50%;background:var(--navy)}
.brand-name{font-weight:700;text-transform:uppercase;letter-spacing:.3px;white-space:nowrap}
.nav a{position:absolute;top:43px;font-size:16px;color:var(--navy);text-decoration:none}
.hero-title{top:168px;font-size:37px;font-weight:400}
.hero-sub{top:216px;font-size:28px;line-height:31px;color:var(--red-text)}
.hero-scene{left:0;top:355px;width:1200px;height:276px;background:linear-gradient(180deg,rgba(255,255,255,0) 0%,rgba(255,255,255,0) 20%,#3f7fa8 45%,#a83a2a 72%,#b1382a 80%,#2d4a6a 86%,#1e3550 100%)}
.section-title{font-size:36px;font-weight:400}
.about-text{top:742px;font-size:16.5px;line-height:25px;color:#1a1a2a}
.service{width:270px;text-align:center}
.service .dome{width:270px;height:158px;background:var(--cyan);border-radius:135px 135px 0 0;position:relative}
.service .art{position:absolute;left:70px;top:4px;width:130px;height:124px;border-radius:6px}
.service h3{font-size:28px;font-weight:400;line-height:33px;margin-top:12px;color:var(--navy)}
.service p{position:absolute;top:250px;left:-10px;width:290px;font-size:20px;line-height:24px;color:#111}
.why{width:300px;text-align:center;color:var(--white)}
.why .ring{width:152px;height:152px;border:1.5px solid #e8e8e8;border-radius:50%;margin:0 auto;display:flex;align-items:center;justify-content:center}
.why h4{font-size:20px;font-weight:600;margin-top:26px}
.why p{font-size:20px;line-height:24px;margin-top:8px}
.partner{top:2354px;width:209px;height:98px;border:1px solid var(--line);display:flex;align-items:center;justify-content:center;background:var(--white)}
.partner span{display:block;width:120px;height:34px;border-radius:6px}
.pride{top:2652px;font-size:20.5px;line-height:27px}
.welcome{top:2759px;font-size:19px}
.domain{top:2788px;font-size:42px}
.follow{left:158px;top:2955px;font-size:16px;color:var(--white)}
.social{top:2950px;width:34px;height:34px;border:1.5px solid var(--white);border-radius:50%}
.foot-head{font-size:15px;color:var(--white);letter-spacing:.3px;font-weight:400}
.foot-head::after{content:"";display:block;width:82px;height:2px;background:var(--red);margin-top:6px}
.foot-text{font-size:14.5px;line-height:20px;color:#e6e8f5}
.foot-links a{display:block;font-size:14.5px;color:#e6e8f5;text-decoration:none;height:31px}
.foot-contact{font-size:12.5px;color:#e6e8f5;display:flex;align-items:center;gap:14px;white-space:nowrap}
.newsletter-input{left:815px;top:3202px;width:225px;height:39px;background:#e6e6e6;border:1px solid #ccc;font-size:11.5px;color:#333;padding-left:9px;display:flex;align-items:center}
</style>
</head>
<body>

<svg class="backdrop" width="1200" height="3384" viewBox="0 0 1200 3384" aria-hidden="true">
  <defs>
    <linearGradient id="sky" x1="0" y1="0" x2="0" y2="1">
      <stop offset="0" stop-color="#b3d1fb"/>
      <stop offset="1" stop-color="#dbe8fb"/>
    </linearGradient>
  </defs>
  <rect x="0" y="0" width="1200" height="631" fill="url(#sky)"/>
  <rect x="0" y="631" width="1200" height="470" fill="#dde9fb"/>
  <path d="M0 1085 Q600 912 1200 1085 V1600 H0Z" fill="#ffffff"/>
  <path d="M0 1585 Q600 1761 1200 1585 V2197 H0Z" fill="#2b2b2b"/>
  <rect x="0" y="2563" width="1200" height="368" fill="#f6f9f0"/>
  <rect x="0" y="2931" width="1200" height="72" fill="#1c2a7a"/>
  <rect x="0" y="3003" width="1200" height="381" fill="#0c0f4a"/>
</svg>

<header>
  <div class="abs brand-mark" style="left:150px;top:8px;width:150px">
    <span class="dot" style="width:62px;height:62px"></span>
    <span class="brand-name" style="font-size:10px;margin-top:4px;color:var(--navy)">Harborline Provisions</span>
  </div>
  <nav class="nav">
    <a style="left:587px">About US</a>
    <a style="left:707px">What we do</a>
    <a style="left:846px">Contact</a>
    <a style="left:954px">Giving Back</a>
  </nav>
</header>

<section class="hero">
  <h1 class="abs center hero-title">Welcome For Visiting Harborline Provisions</h1>
  <p class="abs center hero-sub">We purchase goods anywhere and ship<br>them Nationwide and Export.</p>
  <a class="btn" style="left:526px;top:294px;width:150px;height:50px;font-size:18px">Contact Us</a>
  <div class="abs hero-scene" role="img" aria-label="Container cargo ship loaded with stacked shipping containers sailing on the sea"></div>
</section>

<section class="about">
  <h2 class="abs center section-title" style="top:682px">About Us</h2>
  <p class="abs center about-text">Harborline Provisions works with food manufacturers, brand owners, distributors and wholesalers market their<br>products. Retail, Food Service and Industrial ingredients.<br>Founded in 2008, Harborline Provisions started with the distribution of gluten free products understanding the need<br>to provide access to unique flavors and products forthe celiac consumers. From this,<br>we expanded into deli, dairy, groceries, frozen and beverages.</p>
  <a class="btn" style="left:525px;top:887px;width:150px;height:49px;font-size:18px">Learn More</a>
</section>

<section class="services">
  <h2 class="abs center section-title" style="top:1096px">What We Do</h2>
  <div class="abs service" style="left:168px;top:1163px">
    <div class="dome"><div class="art" role="img" aria-label="Supermarket shelf stocked with groceries beside a shop clerk" style="background:#4a8a8a"></div></div>
    <h3>Sales &amp; Marketing</h3>
    <p>we connect food buyers and sellers through a dedicated approach.</p>
  </div>
  <div class="abs service" style="left:467px;top:1163px">
    <div class="dome"><div class="art" role="img" aria-label="Wooden market stall with fresh fruit and vegetables" style="background:#8a4a2a"></div></div>
    <h3>Trading</h3>
    <p>we purchase goods anywhere and ship them Nationwide and Export</p>
  </div>
  <div class="abs service" style="left:766px;top:1163px">
    <div class="dome"><div class="art" role="img" aria-label="Forklift carrying a pallet of stacked cardboard boxes" style="background:#d9a36a;width:170px;left:50px"></div></div>
    <h3>Closeout/Excess<br>Inventory</h3>
    <p>we buy closeouts and excess inventory for prisons, outlet stores and discounters.</p>
  </div>
  <a class="btn" style="left:525px;top:1517px;width:150px;height:50px;font-size:18px">Learn More</a>
</section>

<section class="why-us">
  <h2 class="abs center section-title" style="top:1763px;color:var(--white)">Why Choose Us</h2>
  <div class="abs why" style="left:142px;top:1826px">
    <div class="ring">
      <svg width="62" height="62" viewBox="0 0 62 62" fill="none" stroke="#fff" stroke-width="3"><path d="M20 24 H8 V56 H54 V24 H42"/><path d="M31 40 V6 M21 16 L31 6 L41 16"/></svg>
    </div>
    <h4>Nationwide and Export</h4>
    <p>we connect food buyers and sellers through a dedicated approach.</p>
  </div>
  <div class="abs why" style="left:449px;top:1826px">
    <div class="ring">
      <svg width="80" height="70" viewBox="0 0 80 70" fill="none" stroke="#fff" stroke-width="3"><rect x="12" y="6" width="56" height="10"/><rect x="12" y="24" width="56" height="10"/><path d="M8 44 H72 M4 64 H76 M26 44 V64 M54 44 V64 M30 52 H50 V64"/></svg>
    </div>
    <h4>Brand Owners</h4>
    <p>we connect food buyers and sellers through a dedicated approach.</p>
  </div>
  <div class="abs why" style="left:750px;top:1826px">
    <div class="ring">
      <svg width="76" height="84" viewBox="0 0 76 84" fill="none" stroke="#fff" stroke-width="3"><circle cx="38" cy="32" r="26"/><circle cx="38" cy="32" r="17"/><path d="M38 22 L41 29 L48 30 L43 35 L44 42 L38 38 L32 42 L33 35 L28 30 L35 29Z"/><path d="M20 52 L8 74 L20 72 L26 82 L34 58 M56 52 L68 74 L56 72 L50 82 L42 58"/></svg>
    </div>
    <h4>Good Quality</h4>
    <p>we connect food buyers and sellers through a dedicated approach.</p>
  </div>
</section>

<section class="partners">
  <h2 class="abs section-title" style="left:0;width:1270px;text-align:center;top:2283px">Our Partners</h2>
  <div class="abs partner" style="left:156px"><span style="background:#2aa6c8"></span></div>
  <div class="abs partner" style="left:382px"><span style="background:#1d2430"></span></div>
  <div class="abs partner" style="left:607px"><span style="background:#e23a2a"></span></div>
  <div class="abs partner" style="left:833px"><span style="background:#4aa832"></span></div>
</section>

<section class="closing">
  <p class="abs center pride">We pride ourselves in working in aneasy, personal and accessible environment making our<br>customers and vendors comfortable with us.We look forward to<br>connecting with you and evaluating how we can assist you reaching your sales objectives</p>
  <p class="abs center welcome">Welcome and thank you for visiting</p>
  <p class="abs center domain">harborlineprovisions.com</p>
</section>

<section class="follow-band">
  <span class="abs follow">Follow News from</span>
  <span class="abs social" style="left:329px"></span>
  <span class="abs social" style="left:368px"></span>
  <span class="abs social" style="left:406px"></span>
  <span class="abs social" style="left:446px"></span>
  <a class="btn" style="left:878px;top:2944px;width:164px;height:49px;font-size:15px;font-weight:700">REQUEST A QUOTE</a>
</section>

<footer>
  <div class="abs brand-mark" style="left:148px;top:3049px;width:190px">
    <span class="dot" style="width:100px;height:100px;background:var(--white)"></span>
    <span class="brand-name" style="font-size:12.5px;margin-top:8px;color:var(--white)">Harborline Provisions</span>
  </div>
  <div class="abs foot-contact" style="left:156px;top:3181px">
    <svg width="12" height="12" viewBox="0 0 24 24" fill="#fff"><path d="M6.6 10.8a15.1 15.1 0 006.6 6.6l2.2-2.2c.3-.3.7-.4 1-.2 1.1.4 2.3.6 3.6.6.6 0 1 .4 1 1V20c0 .6-.4 1-1 1A17 17 0 013 4c0-.6.4-1 1-1h3.5c.6 0 1 .4 1 1 0 1.3.2 2.5.6 3.6.1.3 0 .7-.2 1z"/></svg>
    <span>Call us: +1.555.010.0199</span>
  </div>
  <div class="abs foot-contact" style="left:156px;top:3204px">
    <svg width="12" height="10" viewBox="0 0 24 18" fill="none" stroke="#fff" stroke-width="2.5"><rect x="1" y="1" width="22" height="16"/><path d="M1 1 L12 10 L23 1"/></svg>
    <span>Email: desk@hlprov.com</span>
  </div>
  <p class="abs foot-text" style="left:156px;top:3240px;width:200px;font-size:12px;line-height:18px">Copyright©2020 hlprov.com.<br>All Rights Reserved.</p>

  <div class="abs" style="left:381px;top:3088px">
    <h5 class="foot-head">COMPANY</h5>
  </div>
  <p class="abs foot-text" style="left:380px;top:3138px;width:210px">Harborline Provisions works with food manufacturers, brand owners, distributors and wholesalers market their products. Retail, Food Service and Industrial ingredients.</p>

  <div class="abs" style="left:634px;top:3088px">
    <h5 class="foot-head">COMPANY</h5>
  </div>
  <div class="abs foot-links" style="left:636px;top:3142px">
    <a>About US</a><a>What we do</a><a>Contact</a><a>Giving Back</a>
  </div>

  <div class="abs" style="left:818px;top:3088px">
    <h5 class="foot-head">NEWSLETTER</h5>
  </div>
  <p class="abs foot-text" style="left:816px;top:3143px;width:240px;font-size:12.5px;line-height:21px">Subscribe to our newsletter to receive exclusive offers and wedding tips.</p>
  <div class="abs newsletter-input">Enter Your mail ID</div>
  <a class="btn" style="left:816px;top:3249px;width:150px;height:50px;font-size:16px;font-weight:700">SUBMIT NOW</a>
</footer>

</body>
</html>
```